Luxury Wine Label for New Startup Winery

We need a wine label for our new winery startup. We have worked with a local designer but do not feel the resulting label / logo have the elevation required to present our brand as a luxury wine. Our winery is called "Quailbrook Vineyards" and we are focused on extremely high quality hand crafted artisan and estate wines from the Pacific Northwest.
We would like to see designs that utilize a tree line, or other imagery that represents the "Quailbrook" part of our company name. Another interesting feature could be wood grain.
A logo will be required based on your design so please design with this in mind:
This logo should be consistent with the wine bottle label design, and should be representative of our high end exclusive wine while giving a sense of place (Oregon/ Pacific Northwest.)
I will supply an image of the design we received from our local designer, PLEASE NOTE: in general we do like wood grain and tree line concepts but feel the execution was poorly done.
ATTN: Logo design should be suitable for use on: Bottles (Red wine/rose/white wine), Bussiness cards, vehicle signage, business signage, etc
P.S.:
If you have a design that is not outside the box we are still interested in seeing it.
Label is for a burgundy style bottle with a label height of 3.5 - 4" and a width of 3.5-4"
any label <= 4"x4" and >=3.5"x3.5" will be acceptable:
HOWEVER Width should be greater than or equal to height due to the bottle format
Target Market(s)
Wine enthusiasts with adequate discretionary budgets to afford $100 bottles of wine.
Industry/Entity Type
Wine / Winery
Requirements
Must have
- A sense of luxury, a feel of exclusivity, and a theme consistent with our product and brand name
Nice to have
- Tree line, wood grain or other wood themes. Serif fonts
Should not have
- anything cheesy, off topic, hard to read script fonts or anything that makes the label hard to read from a few feet away or too busy

```html
<!DOCTYPE html>
<html lang="en">
<head>
<meta charset="utf-8">
<title>Quailbrook Vineyards – Label Designs</title>
<link href="https://fonts.googleapis.com/css2?family=Lato:wght@300;400&family=Roboto+Slab:wght@500;600;800&display=swap" rel="stylesheet">
<style>
  :root {
    --backdrop: #707070;
    --paper: #fbf3d9;
    --paper-glow: #fffdf6;
    --grain-deep: #5a4c3c;
    --grain-mid: #b9a783;
    --grain-light: #eadfbd;
    --ink: #231f20;
    --red: #9b1b20;
    --rose: #e89c8e;
    --white: #ffffff;
    --title: #f4f4f4;
  }
  * { box-sizing: border-box; margin: 0; padding: 0; }
  html, body { width: 1200px; height: 857px; overflow: hidden; }
  body { background: var(--backdrop); position: relative; font-family: "Roboto Slab", serif; }

  .label {
    position: absolute; top: 258px; width: 340px; height: 340px;
    background: radial-gradient(ellipse at 55% 50%, var(--paper-glow) 0%, var(--paper) 78%);
    box-shadow: 2px 3px 6px rgba(0,0,0,.5);
    overflow: hidden;
  }
  .label--red { left: 67px; --accent: var(--red); }
  .label--rose { left: 427px; --accent: var(--rose); }
  .label--white { left: 788px; --accent: var(--white); }

  .grain-band { position: absolute; left: 0; width: 100%; height: 52px; }
  .grain-band--top {
    top: 0;
    background:
      repeating-linear-gradient(180deg, rgba(58,48,38,.0) 0 6px, rgba(58,48,38,.10) 6px 7px),
      linear-gradient(180deg, var(--grain-deep) 0%, var(--grain-mid) 30%, var(--grain-light) 75%, var(--paper) 100%);
  }
  .grain-band--bottom {
    bottom: 0;
    background:
      repeating-linear-gradient(180deg, rgba(58,48,38,.0) 0 6px, rgba(58,48,38,.10) 6px 7px),
      linear-gradient(0deg, var(--grain-deep) 0%, var(--grain-mid) 30%, var(--grain-light) 75%, var(--paper) 100%);
  }

  .brand-panel {
    position: absolute; left: 81px; top: 66px; width: 178px; height: 112px;
    background: var(--accent); border-radius: 7px;
    display: flex; align-items: center; justify-content: center; gap: 9px;
  }
  .label--white .brand-panel { box-shadow: 1px 2px 4px rgba(0,0,0,.35); }
  .brand-panel__mark { width: 12px; height: 12px; background: var(--ink); flex: none; }
  .brand-panel__name {
    font-weight: 800; color: var(--ink); text-transform: uppercase; text-align: center;
    display: flex; flex-direction: column; line-height: 1.1;
  }
  .brand-panel__line1 { font-size: 20px; letter-spacing: .5px; }
  .brand-panel__line2 { font-size: 13px; letter-spacing: 2.5px; }

  .region {
    position: absolute; left: 0; width: 100%; top: 192px; text-align: center;
    font-weight: 600; font-size: 16px; color: var(--ink);
  }
  .varietal {
    position: absolute; left: 0; width: 100%; top: 211px; text-align: center;
    font-weight: 600; font-size: 20px; color: var(--accent); letter-spacing: .3px;
  }
  .label--white .varietal {
    text-shadow: 0 0 1px #555, 1px 1px 2px rgba(0,0,0,.45);
  }
  .volume {
    position: absolute; left: 104px; width: 132px; top: 263px; height: 20px;
    border-top: 1px solid var(--ink); border-bottom: 1px solid var(--ink);
    text-align: center; font-size: 11.5px; font-weight: 500; line-height: 18px; color: var(--ink);
  }

  .heading {
    position: absolute; left: 0; width: 100%; top: 683px; text-align: center;
    font-family: "Lato", sans-serif; color: var(--title);
  }
  .heading__title {
    font-weight: 400; font-size: 49px; line-height: 53px; letter-spacing: 6px;
    text-transform: uppercase;
  }
  .heading__note {
    margin-top: 9px; font-size: 16px; letter-spacing: 2px; font-variant: small-caps;
  }
</style>
</head>
<body>

<section class="label label--red">
  <div class="grain-band grain-band--top" role="img" aria-label="Wood grain pattern with scattered vine leaves"></div>
  <div class="brand-panel"><span class="brand-panel__mark"></span><span class="brand-panel__name"><span class="brand-panel__line1">Quailbrook</span><span class="brand-panel__line2">Vineyards</span></span></div>
  <p class="region">Pacific Northwest</p>
  <p class="varietal">RED WINE</p>
  <p class="volume">12.5%Vol / 750 Ml</p>
  <div class="grain-band grain-band--bottom" role="img" aria-label="Wood grain pattern with scattered vine leaves"></div>
</section>

<section class="label label--rose">
  <div class="grain-band grain-band--top" role="img" aria-label="Wood grain pattern with scattered vine leaves"></div>
  <div class="brand-panel"><span class="brand-panel__mark"></span><span class="brand-panel__name"><span class="brand-panel__line1">Quailbrook</span><span class="brand-panel__line2">Vineyards</span></span></div>
  <p class="region">Pacific Northwest</p>
  <p class="varietal">ROSE WINE</p>
  <p class="volume">12.5%Vol / 750 Ml</p>
  <div class="grain-band grain-band--bottom" role="img" aria-label="Wood grain pattern with scattered vine leaves"></div>
</section>

<section class="label label--white">
  <div class="grain-band grain-band--top" role="img" aria-label="Wood grain pattern with scattered vine leaves"></div>
  <div class="brand-panel"><span class="brand-panel__mark"></span><span class="brand-panel__name"><span class="brand-panel__line1">Quailbrook</span><span class="brand-panel__line2">Vineyards</span></span></div>
  <p class="region">Pacific Northwest</p>
  <p class="varietal">WHITE WINE</p>
  <p class="volume">12.5%Vol / 750 Ml</p>
  <div class="grain-band grain-band--bottom" role="img" aria-label="Wood grain pattern with scattered vine leaves"></div>
</section>

<header class="heading">
  <h1 class="heading__title">Quailbrook Vineyards<br>Label Designs</h1>
  <p class="heading__note">Any changes in these designs are accept</p>
</header>

</body>
</html>
```